MBRDC redesign and update stationary bc envelopes.

Stationary, Envelopes, Brochures, Business Card. Need to add second surgeon and two other offices. I need everything to match. I am a oral & maxillofacial surgeon.
Additional surgeon and three office addresses.
Jae Min Park, DMD, MD, INC

3718 Silver Meadow Parkway
El Dorado Hills, CA 95762

642 Lorin Way, Suite 101
Folsom, CA. 95630

2317 Vale Street, Suite 105
Auburn, CA. 95603
Updates

Logo design uploaded. Zapfino Extra/Adobe Garamond/Palatino are fonts used before. Not sure what is on exisiting stationary.

Target Market(s)

Referral dentist and sometimes patients. I am a oral & Maxillofacial surgeon.

Industry/Entity Type

Dental Clinic

Font styles to use
Serif
Script

Requirements
Must have
• Color of existing stationary. Update is possible.
Nice to have
• Conservative/modern
Should not have
• Playful

```html
<!DOCTYPE html>
<html lang="en">
<head>
<meta charset="utf-8">
<title>MBRDC Stationery</title>
<link href="https://fonts.googleapis.com/css2?family=Tinos&family=Arimo&family=Open+Sans&display=swap" rel="stylesheet">
<style>
:root{
  --bg:#e4e4e4;
  --paper:#ffffff;
  --green:#6e8b23;
  --green-dark:#5f7a1d;
  --green-light:#8a9f45;
  --brown:#6b4f3e;
  --ink:#1e1e1e;
  --body:#4a4a4a;
  --label:#8c8c8c;
  --hill:#f1e6a6;
  --sky:#d9e7ee;
}
*{margin:0;padding:0;box-sizing:border-box}
html,body{width:1200px;height:769px;overflow:hidden;background:var(--bg)}
.canvas{position:relative;width:1200px;height:769px}
.sheet{position:absolute;background:var(--paper);box-shadow:0 2px 6px rgba(0,0,0,.18);overflow:hidden}
.serif{font-family:"Tinos",serif}
.sans{font-family:"Arimo",sans-serif}
.brand{font-family:"Tinos",serif;color:var(--green);display:flex;align-items:center;gap:6px;line-height:1}
.brand .dot{width:10px;height:10px;border-radius:50%;background:var(--green)}
.doctor{font-family:"Tinos",serif;color:var(--green)}
.credential{font-family:"Arimo",sans-serif;color:var(--ink)}
.abs{position:absolute}

/* letterhead */
.letterhead{left:87px;top:100px;width:437px;height:560px}
.letterhead .brand{left:42px;top:40px;font-size:26px}
.letterhead .divider{left:256px;top:15px;width:1px;height:68px;background:#888}
.letterhead .contact{left:267px;top:12px;font-size:6.6px;line-height:8.1px}
.letterhead .contact .doctor{font-size:8.2px;line-height:10px}
.contact .row{display:flex;align-items:center;gap:3px;font-family:"Arimo",sans-serif;color:var(--ink)}
.contact svg{width:6px;height:6px;fill:var(--green)}
.letter{left:41px;top:101px;width:356px;font-family:"Open Sans",sans-serif;font-size:7px;color:var(--body)}
.letter p{line-height:12.6px;margin-bottom:12.6px;text-align:justify}
.letter .meta{line-height:8.4px;margin-bottom:0}
.signature{width:100px;height:14px;background:linear-gradient(90deg,#f2f2f2,#e8e8e8);margin:6px 0 6px}
.signer{font-size:8.6px;color:#333}
.services{left:0;width:100%;background:var(--brown);color:#fff;font-family:"Arimo",sans-serif;text-align:center}
.offices{left:0;width:100%;background:var(--green);color:#fff;font-family:"Arimo",sans-serif;display:flex;justify-content:center;align-items:center}
.offices .office{text-align:center;padding:0 10px}
.offices .office + .office{border-left:1px solid rgba(255,255,255,.6)}
.letterhead .services{top:495px;height:29px;font-size:7.4px;line-height:10px;padding-top:5px}
.letterhead .offices{top:526px;height:34px;font-size:7.4px;line-height:9.6px}

/* envelope */
.envelope-label{left:815px;top:125px;font-family:"Arimo",sans-serif;font-size:18px;color:var(--label)}
.envelope{left:597px;top:171px;width:507px;height:229px}
.envelope .brand{left:14px;top:36px;font-size:20px}
.envelope .return{left:17px;top:69px;font-size:6.6px;line-height:8.3px}
.envelope .return .doctor{font-size:8.2px;line-height:10px}
.envelope .web{left:14px;top:125px;font-family:"Tinos",serif;font-size:7.4px;letter-spacing:.8px;color:#555}
.envelope .services{top:165px;height:32px;font-size:8.2px;line-height:10.6px;padding-top:6px}
.envelope .offices{top:199px;height:30px;font-size:8.2px;line-height:10px}

/* card front */
.card-front{left:607px;top:487px;width:233px;height:138px}
.card-front .hills{left:0;top:78px;width:233px;height:60px;background:linear-gradient(170deg,rgba(255,255,255,0) 20%,var(--hill) 55%,#f6efc6 100%)}
.card-front .contact{left:11px;top:13px;font-size:5.6px;line-height:8.3px}
.card-front .contact .doctor{font-size:8px;line-height:10.5px}
.card-front .brand{left:134px;top:40px;font-size:18px}
.card-front .phones{left:11px;top:69px;font-size:6px;line-height:8.5px}
.card-front .email{left:113px;top:86px;font-family:"Arimo",sans-serif;font-style:normal;font-size:5.8px;color:var(--ink)}
.card-front .web{left:15px;top:116px;font-family:"Tinos",serif;font-size:6.2px;letter-spacing:.8px;color:#6a6a4a}

/* card back */
.card-back{left:862px;top:487px;width:233px;height:138px;background:linear-gradient(120deg,var(--green-light),var(--green) 55%,#7a7a3a)}
.card-back .brand{left:16px;top:28px;font-size:24px;color:#fff}
.card-back .brand .dot{background:#fff}
.card-back .service-list{left:11px;top:72px;list-style:none;font-family:"Arimo",sans-serif;font-size:5.6px;line-height:8.5px;color:#fff}
.card-back .service-list li::before{content:"";display:inline-block;width:3px;height:3px;border-radius:50%;background:#fff;margin-right:3px;vertical-align:middle}
.card-back .locations{right:13px;top:78px;text-align:right;font-family:"Arimo",sans-serif;font-size:5.6px;line-height:8.3px;color:#fff}
.card-back .locations .loc{margin-bottom:2px;position:relative;padding-right:0}
.card-back .locations svg{position:absolute;right:-8px;top:1px;width:5px;height:7px;fill:#f0e9a8}
</style>
</head>
<body>
<div class="canvas">

  <!-- Letterhead -->
  <section class="sheet letterhead">
    <div class="abs brand"><span class="dot"></span>MBRDC</div>
    <div class="abs divider"></div>
    <div class="abs contact">
      <div class="doctor">Martin R. Halvorsen, DDS, Inc.</div>
      <div class="credential">Diplomate of the American Board of<br>Oral &amp; Maxillofacial Surgery</div>
      <div class="doctor" style="margin-top:2px">Jae Min Park, DMD, MD, INC</div>
      <div class="credential">Dental Implant and Oral Surgery</div>
      <div class="row" style="margin-top:3px">
        <svg viewBox="0 0 10 10"><path d="M2 0h2l1 3-1.5 1a6 6 0 0 0 2.5 2.5L7 5l3 1v2a2 2 0 0 1-2 2C4 10 0 6 0 2a2 2 0 0 1 2-2z"/></svg>916.555.0142
        <svg viewBox="0 0 10 10" style="margin-left:3px"><rect x="2" y="0" width="6" height="3"/><rect x="0" y="3.5" width="10" height="4"/><rect x="2" y="8" width="6" height="2"/></svg>916.555.0187
      </div>
      <div class="row"><svg viewBox="0 0 10 10"><path d="M0 2h10v6H0z"/></svg>drhalvorsen@meadowridgeoralsurgery.com</div>
      <div class="row"><svg viewBox="0 0 10 10"><circle cx="5" cy="5" r="5"/></svg>www.meadowridgeoralsurgery.com</div>
    </div>

    <div class="abs letter">
      <p class="meta">Issuing Date: May 5, 2018</p>
      <p class="meta" style="margin-top:8px">Name Of Employee Mr. XYZABC<br>Address of Employee<br>Address Line 2 etc..</p>
      <p style="margin-top:22px">Dear Mr.XYZABC</p>
      <p>Lorem Ipsum has been the industry's standard dummy text ever since the 1500s, when an unknown printer took a galley of type and scrambled it to make a type specimen book. It has survived not only five centuries, but also the leap into electronic typesetting, remaining essentially unchanged. It was popularised in the 1960s with the release of Letraset sheets containing Lorem Ipsum passages, and more recently with desktop publishing software like Aldus PageMaker including versions of Lorem Ipsum.</p>
      <p>Lorem Ipsum is simply dummy text of the printing and typesetting industry. Lorem Ipsum has been the industry's standard dummy text ever since the 1500s, when an unknown printer took a galley of type and scrambled it to make a type specimen book.</p>
      <p>It has survived not only five centuries, but also the leap into electronic typesetting, remaining essentially unchanged. It was popularised in the 1960s with the release of Letraset sheets containing Lorem IpsumIpsum passages.</p>
      <p style="margin:24px 0 0">Yours Sincerely</p>
      <div class="signature" role="img" aria-label="Handwritten signature"></div>
      <div class="signer">Elaine Porter</div>
      <div style="margin-top:3px">Managing Director</div>
    </div>

    <div class="abs services">Dentoalveolar Surgery ● Dental Implant Surgery ● Orthognathic Surgery ● Facial Trauma Surgery<br>Preprosthetic and Reconstructive Surgery ● TMJ Disorders and Surgery ● Obstructive Sleep Apnea Surgery</div>
    <div class="abs offices">
      <div class="office">3718 Silver Meadow Parkway<br>El Dorado Hills, CA 95762</div>
      <div class="office">642 Lorin Way, Suite 101<br>Folsom, CA. 95630</div>
      <div class="office">2317 Vale Street, Suite 105<br>Auburn, CA. 95603</div>
    </div>
  </section>

  <!-- Envelope -->
  <div class="abs envelope-label">Envelope</div>
  <section class="sheet envelope">
    <div class="abs brand"><span class="dot"></span>MBRDC</div>
    <div class="abs return">
      <div class="doctor">Martin R. Halvorsen, DDS, Inc.</div>
      <div class="credential">Diplomate of the American Board of<br>Oral &amp; Maxillofacial Surgery</div>
      <div class="doctor" style="margin-top:3px">Jae Min Park, DMD, MD, INC</div>
      <div class="credential">Dental Implant and Oral Surgery</div>
    </div>
    <div class="abs web">www.meadowridgeoralsurgery.com</div>
    <div class="abs services">Dentoalveolar Surgery ● Dental Implant Surgery ● Orthognathic Surgery ● Facial Trauma Surgery<br>Preprosthetic and Reconstructive Surgery ● TMJ Disorders and Surgery ● Obstructive Sleep Apnea Surgery</div>
    <div class="abs offices">
      <div class="office">3718 Silver Meadow Parkway<br>El Dorado Hills, CA 95762</div>
      <div class="office">642 Lorin Way, Suite 101<br>Folsom, CA. 95630</div>
      <div class="office">2317 Vale Street, Suite 105<br>Auburn, CA. 95603</div>
    </div>
  </section>

  <!-- Business card front -->
  <section class="sheet card-front">
    <div class="abs hills" role="img" aria-label="Soft rolling hills backdrop"></div>
    <div class="abs contact">
      <div class="doctor">Martin R. Halvorsen, DDS, Inc.</div>
      <div class="credential">Diplomate of the American Board of<br>Oral &amp; Maxillofacial Surgery</div>
      <div class="doctor" style="margin-top:2px">Jae Min Park, DMD, MD, INC</div>
      <div class="credential">Dental Implant and Oral Surgery</div>
    </div>
    <div class="abs brand"><span class="dot"></span>MBRDC</div>
    <div class="abs contact phones">
      <div class="row"><svg viewBox="0 0 10 10"><path d="M2 0h2l1 3-1.5 1a6 6 0 0 0 2.5 2.5L7 5l3 1v2a2 2 0 0 1-2 2C4 10 0 6 0 2a2 2 0 0 1 2-2z"/></svg>916.555.0142</div>
      <div class="row"><svg viewBox="0 0 10 10"><rect x="2" y="0" width="6" height="3"/><rect x="0" y="3.5" width="10" height="4"/><rect x="2" y="8" width="6" height="2"/></svg>916.555.0187</div>
    </div>
    <div class="abs email">drhalvorsen@meadowridgeoralsurgery.com</div>
    <div class="abs web">www.meadowridgeoralsurgery.com</div>
  </section>

  <!-- Business card back -->
  <section class="sheet card-back">
    <div class="abs brand"><span class="dot"></span>MBRDC</div>
    <ul class="abs service-list">
      <li>Dentoalveolar Surgery</li>
      <li>Dental Implant Surgery</li>
      <li>Orthognathic Surgery</li>
      <li>Facial Trauma Surgery</li>
      <li>Preprosthetic and Reconstructive Surgery</li>
      <li>TMJ Disorders and Surgery</li>
      <li>Obstructive Sleep Apnea Surgery</li>
    </ul>
    <div class="abs locations">
      <div class="loc">3718 Silver Meadow Parkway<svg viewBox="0 0 10 14"><path d="M5 0a5 5 0 0 1 5 5c0 4-5 9-5 9S0 9 0 5a5 5 0 0 1 5-5zm0 3a2 2 0 1 0 0 4 2 2 0 0 0 0-4z"/></svg><br>El Dorado Hills, CA 95762</div>
      <div class="loc">2317 Vale Street, Suite 105<svg viewBox="0 0 10 14"><path d="M5 0a5 5 0 0 1 5 5c0 4-5 9-5 9S0 9 0 5a5 5 0 0 1 5-5zm0 3a2 2 0 1 0 0 4 2 2 0 0 0 0-4z"/></svg><br>Auburn, CA. 95603</div>
      <div class="loc">642 Lorin Way, Suite 101<svg viewBox="0 0 10 14"><path d="M5 0a5 5 0 0 1 5 5c0 4-5 9-5 9S0 9 0 5a5 5 0 0 1 5-5zm0 3a2 2 0 1 0 0 4 2 2 0 0 0 0-4z"/></svg><br>Folsom, CA. 95630</div>
    </div>
  </section>

</div>
</body>
</html>
```